Maine Organic farm needs a label design for various food products

We need a label design that we can use across a variety of vegetable-based food products that we produce using some of our organic vegetables that we grow on our farm located in Maine, USA.
Our products include:
1) a Traditional and Vegan Korean Kimchi
2) Sumel Sauce (a Korean Hot Sauce)
3) Pickles of Brambleton Relish
4) Brinjalista Chutney
5) Seasonal Soups (many varieties, depending on what's available during the season)
6) Firm Ranks Maple Syrup (we are retired from the Coastal Lancer Guard, hence the name and spelling)
7) Maine Wild Blueberry Kombucha (made with organic Maine wild blueberries)

For the Korean products (kimchi and Sumel Sauce) we would like to incorporate the Korean chili pepper (red) and chopsticks. The attached picture was taken from the internet, it has not been trademarked, but I am hesitant to use it as is as our business expands. Would like the "kimchi" to somehow incorporate the chopstick and pepper, but not look exactly like the attached image.

The final design should communicate farm fresh, organic, healthy and high quality ingredients, and Maine-made. All of our products go into glass jars 16oz and 8 oz. The hot sauce goes into 5.5oz and 8 oz bottles, the Maple Syrup goes into 8oz and 16oz bottles, and a 12oz bottle for the Kombucha. We will need the flexibility of changing some components of the label to accommodate each different food product.

The labels do not have the encircle the entirety of the jar. We understand that this is a tall order to fit so many different products. We are hoping that once we get the feel and design down, we can work with you for a fee outside of the competition to finalize other products labels on different sizes jars, bottles, etc. Its most important that we get the right feel for a label that can be used for a wide variety of food products.

Target Market(s)

Health conscious, foodies, local farm supporters

Font styles to use
Serif
Decorative
Script

Colors

Designer to choose colors to be used in the design.

Requirements
Must have
• Wendle Brook Farm Logo. Room for product name (interchangeable per product), ingredients list, space for jar size (8 oz, 12 oz, 16 oz). On Korean products -must have Korean hot chili pepper and chopsticks
Nice to have
• We'd like something fairly bold and rustic looking.
Should not have
• Nothing too modern or industrial looking. Nothing hippy-ish. Clean and professional. No cartoonish looking letters or designs.

```html
<!DOCTYPE html>
<html lang="en">
<head>
<meta charset="utf-8">
<title>Wendle Brook Farm – Vegan Kombucha Label</title>
<link rel="stylesheet" href="https://fonts.googleapis.com/css2?family=Oswald:wght@400;500;600&family=Mr+Dafoe&display=swap">
<style>
  :root {
    --backdrop: #e6e7e9;
    --kraft: #cdbb95;
    --cream: #efece6;
    --navy: #1f3d5c;
    --berry: #c0282f;
    --maroon: #8f2f3e;
    --rose: #b9737c;
    --ink: #2a2a2a;
    --sketch: #d9d6cf;
    --tea: #e5b23a;
  }
  * { margin: 0; padding: 0; box-sizing: border-box; }
  html, body { width: 1200px; height: 1038px; overflow: hidden; background: var(--backdrop); }
  .label {
    position: absolute; left: 100px; top: 239px;
    width: 1000px; height: 560px; overflow: hidden;
    font-family: "Oswald", sans-serif; color: var(--ink);
    box-shadow: 0 6px 20px rgba(0,0,0,.12);
  }
  .label-shapes { position: absolute; inset: 0; }
  .brand { position: absolute; left: 140px; top: 24px; width: 340px; text-align: center; }
  .brand-mark { width: 66px; height: 66px; border: 3px solid var(--maroon); border-radius: 50%; margin: 0 auto 6px; }
  .brand-name { font-weight: 500; font-size: 28px; color: var(--navy); letter-spacing: 1px; line-height: 1; white-space: nowrap; }
  .product-type { position: absolute; left: 160px; top: 140px; width: 300px; text-align: center;
    font-weight: 600; font-size: 74px; color: var(--navy); letter-spacing: 1px; line-height: 1; }
  .product-name { position: absolute; left: 150px; top: 212px; width: 440px; white-space: nowrap;
    font-family: "Mr Dafoe", cursive; font-size: 100px; color: var(--berry); line-height: 1; transform: rotate(-6deg); }
  .net-weight { position: absolute; left: 560px; top: 440px; width: 100px; text-align: center;
    font-weight: 500; font-size: 20px; line-height: 1.15; color: var(--ink); }
  .info { position: absolute; left: 660px; top: 44px; width: 300px; font-size: 19px; line-height: 1.35; }
  .info p { margin-bottom: 14px; }
  .made-in { font-family: "Mr Dafoe", cursive; font-size: 46px; color: var(--maroon); line-height: 1; margin-bottom: 10px; }
  .farm-line { font-weight: 600; letter-spacing: 1px; }
  .cert-box { position: absolute; left: 700px; top: 430px; width: 170px; height: 80px; background: #fff;
    display: flex; align-items: center; justify-content: center; font-weight: 500; font-size: 20px; color: var(--navy); }
</style>
</head>
<body>
<div class="label">
  <svg class="label-shapes" width="1000" height="560" viewBox="0 0 1000 560">
    <rect width="1000" height="560" fill="var(--kraft)"/>
    <path d="M0,0 H640 C740,200 660,500 320,530 C190,540 80,520 0,500 Z" fill="var(--rose)"/>
    <path d="M0,0 H616 C712,200 640,470 310,500 C190,510 80,495 0,470 Z" fill="var(--maroon)"/>
    <path d="M0,0 H590 C680,200 610,445 300,470 C180,478 80,470 0,450 Z" fill="var(--cream)"/>
    <rect x="0" y="230" width="200" height="210" fill="var(--sketch)" opacity=".7" role="img" aria-label="Pencil sketch of a barn, tractor and windmill"/>
    <rect x="120" y="335" width="220" height="115" rx="20" fill="var(--tea)" role="img" aria-label="Photo of three glasses of golden kombucha"/>
  </svg>

  <div class="brand">
    <div class="brand-mark"></div>
    <div class="brand-name">WENDLE BROOK FARM</div>
  </div>
  <div class="product-type">VEGAN</div>
  <div class="product-name">Kombucha</div>
  <div class="net-weight">Netwt<br>12oz/375<br>Grams</div>

  <div class="info">
    <p>Locally grown, locally made.<br>Ingredients: Korean green tea, Hawaiian cane sugar, filtered water, live cultures.</p>
    <div class="made-in">Made in Maine</div>
    <p>Keep refrigerated. Shake gently.</p>
    <p><span class="farm-line">WENDLE BROOK FARM</span><br>12 Orchard Lane, Brookfield, Maine</p>
  </div>
  <div class="cert-box">Certified Organic</div>
</div>
</body>
</html>
```